Design a great website for our amazing new country club in Southern California!

Our old neighborhood golf club is being transformed into a 100% new world-class club located down the street from the old location. We want a new website look that projects our new image. However because the club hasn't been built yet, we don't have a lot of images--just a new logo and a few renderings. So we will add images in the coming months as things get built. In the meantime, for things such as restaurant or swimming or tennis pics, feel free to plug in stock internet images for now. And regarding the movie file, we had an idea for a dramatic headline slowly rising over the clubhouse. It's just an idea, however, we're not married to it. We need to get creative here, as we have so few images. Oh, and we definitely want one main graphic on the home page. We don't like the slide-show effect--looks cheap. And finally, the landing page will be a 'public' page with other pages aimed at attracting new members. There will also be a 'Members area' that is password-protected. Site maps and rough copy for each of the two sections is included. Good luck!! :-) Please view our current website: quillbrookcc.com

Target Market(s)

Wealthy folks who like golf, sports and dining. Our memberships range in price from $18,000 to $130,000.

Industry/Entity Type

Club

Coding

Coded - Design and coding required

Number of Pages Required

5+ page

Font styles to use
Sans Serif

Requirements
Must have
• a GORGEOUS home page, with buttons and features that will remain static on all other pages. We want the navigation buttons along the top with pull-downs. Only the areas below the nav buttons will change. We want this site to look very clean and classy.
Nice to have
• Maybe have the button 'glow' or enlarge or whatever when you roll over them. Whatever can spruce up the simple classy design. Maybe so some special effect to the QB logo as well. As long as it looks classy, that's the main thing. And if you can find some good generic images of golf, dining, swimming, tennis, whatever on the net, feel free to use them.
Should not have
• No slide show effects, with multiple images changing.

```html
<!DOCTYPE html>
<html lang="en">
<head>
<meta charset="utf-8">
<title>Quillbrook Country Club</title>
<link rel="stylesheet" href="https://fonts.googleapis.com/css2?family=Cinzel:wght@400;700&family=Open+Sans:ital,wght@0,400;0,600;0,700;1,400&display=swap">
<style>
:root{
  --green:#5aaa12;
  --ink:#1b1b1b;
  --text:#444;
  --pale:#f5f5f5;
  --line:#dcdcdc;
  --black:#050505;
  --white:#fff;
  --serif:'Cinzel', serif;
  --sans:'Open Sans', sans-serif;
}
*{margin:0;padding:0;box-sizing:border-box}
html,body{width:671px;height:1200px;overflow:hidden;background:var(--white)}
body{position:relative;font-family:var(--sans);color:var(--text)}
.abs{position:absolute}

/* hero */
.hero{left:0;top:0;width:671px;height:344px;
  background:linear-gradient(180deg,#6d97c4 0%,#8fb0cf 18%,#7d8f7a 32%,#4d6a48 48%,#3f5a44 62%,#5c6f80 78%,#8a8a86 100%)}
.utility-bar{right:0;top:0;width:395px;height:22px;background:linear-gradient(#2a2a2a,#000);
  clip-path:polygon(0 0,100% 0,100% 100%,14px 100%);display:flex;justify-content:flex-end;align-items:center;gap:13px;padding-right:36px;
  font-family:var(--serif);font-size:6.4px;color:var(--white);letter-spacing:.2px}
.brand{left:86px;top:30px;width:94px;text-align:center;color:var(--white);font-family:var(--serif);font-weight:400;font-size:10px;line-height:12px;letter-spacing:.4px}
.main-nav{left:230px;top:44px;display:flex;gap:14px;font-family:var(--serif);font-size:7.4px;color:var(--white);letter-spacing:.3px}
.hero-circle{left:304px;top:124px;width:64px;height:64px;border:2.5px solid var(--white);border-radius:50%}
.hero-title{left:0;width:671px;top:198px;text-align:center;font-family:var(--serif);font-size:26px;line-height:32px;color:var(--white);font-weight:700;letter-spacing:.5px}
.hero-sub{left:170px;width:331px;top:234px;text-align:center;font-size:13px;line-height:16px;color:var(--white);font-weight:600}

/* video */
.video-band{left:0;top:344px;width:671px;height:214px;background:var(--pale);border-bottom:1px solid var(--line)}
.video-frame{left:90px;top:370px;width:234px;height:156px;background:linear-gradient(180deg,#8fb4d8 0%,#b9cfe0 30%,#8a8275 55%,#6f6a5c 75%,#5a6a48 100%)}
.play{left:190px;top:430px}
h2.section{font-family:var(--serif);font-weight:400;color:var(--ink);font-size:15px;line-height:18px;letter-spacing:.3px}
.video-lead{left:346px;top:395px;width:230px;font-family:var(--serif);font-size:7.4px;line-height:11px;color:var(--ink)}
.copy{font-size:5.6px;line-height:10.6px;color:var(--text)}
.btn{background:var(--green);color:var(--white);font-size:6.8px;font-weight:700;display:flex;align-items:center;justify-content:center}

/* about */
.about-intro{left:150px;width:371px;top:599px;text-align:center}
.feature-pic{width:114px;height:114px;border-radius:50%;border:2.5px solid var(--green)}
.feature-name{width:124px;text-align:center;font-family:var(--serif);font-size:10px;font-weight:400;color:var(--ink)}
.feature-text{width:104px;text-align:center}
.col-rule{width:1px;height:68px;background:var(--line);top:752px}
.double-rule{left:90px;top:844px;width:491px;height:4px;border-top:1px solid var(--line);border-bottom:1px solid var(--line)}

/* who / testimonials */
.who-pic{left:90px;top:901px;width:148px;height:99px;border:3px solid var(--white);box-shadow:0 0 2px #999;
  background:linear-gradient(160deg,#d6dccc 0%,#9fb07a 40%,#6d8a4e 70%,#b9c2a6 100%)}
.quote{left:432px;top:904px;width:150px;font-style:italic;color:var(--green);font-size:5.6px;line-height:10.4px}
.qmark{font-family:Georgia,serif;color:#aaa;font-size:14px;font-style:normal;line-height:0;vertical-align:-4px}
.cite{left:436px;top:993px;font-family:var(--serif);font-size:7.4px;color:var(--ink)}

/* footer */
.footer{left:0;top:1030px;width:671px;height:136px;background:var(--black)}
.foot-brand{left:90px;top:1088px}
.foot-head{font-size:7.2px;font-weight:700;color:var(--white)}
.foot-rule{width:50px;height:1px;background:var(--white)}
.foot-rule::before{content:"";position:absolute;left:0;top:-2.5px;width:5px;height:5px;background:var(--white);transform:rotate(45deg)}
.foot-list{list-style:none;font-size:5.8px;line-height:10.3px;color:var(--white)}
.newsletter-text{font-size:5.8px;line-height:9.6px;color:var(--white)}
.email{left:437px;top:1113px;width:103px;height:19px;background:var(--white);font-size:5.6px;font-style:italic;color:#555;padding:6px 5px}
.signup{left:540px;top:1113px;width:41px;height:19px}
.bottom-bar{left:0;top:1166px;width:671px;height:34px;background:var(--green)}
.social{top:1174px;width:17px;height:17px;border:1.2px solid var(--white);border-radius:50%}
.legal{left:362px;top:1178px;font-size:5.6px;color:var(--white)}
</style>
</head>
<body>

<header>
  <div class="abs hero" role="img" aria-label="Rendering of the clubhouse pool terrace with cabanas and hillside homes"></div>
  <nav class="abs utility-bar">
    <span>MY ACCOUNT</span><span>MY CLUB</span><span>GOLF</span><span>SPORTS &amp; FITNESS</span><span>DINING &amp; SOCIAL</span><span>LADIES GOLF</span>
  </nav>
  <div class="abs brand">QUILLBROOK<br>COUNTRY CLUB</div>
  <nav class="abs main-nav">
    <span>GUEST INFO</span><span>MEMBERSHIP</span><span>GOLF</span><span>CLUB HOUSE &amp; AMENITIES</span><span>WEDDING &amp; EVENTS</span>
  </nav>
  <div class="abs hero-circle"></div>
  <h1 class="abs hero-title">QUILLBROOK</h1>
  <p class="abs hero-sub">Sed ut perspiciatis unde omnis iste natus errsit vol uptatem accusantiume omnis iste n dolorem.</p>
</header>

<section>
  <div class="abs video-band"></div>
  <div class="abs video-frame" role="img" aria-label="Video still of the new clubhouse terrace"></div>
  <svg class="abs play" width="34" height="34" viewBox="0 0 34 34"><circle cx="17" cy="17" r="15.5" fill="rgba(0,0,0,.15)" stroke="#fff" stroke-width="2"/><path d="M13 10v14l11-7z" fill="#fff"/></svg>
  <h2 class="abs section" style="left:345px;top:369px">OUR VIDEO</h2>
  <p class="abs video-lead">SED UT PERSPICIATIS UNDE OMNIS ISTE NATUS ERROR SIT VOLUPTATEM ACCUSANTIUM DOLOREM.</p>
  <p class="abs copy" style="left:346px;top:425px;width:236px">Sed ut perspiciatis unde omnis iste natus error sit voluptatem accusantium dolorem que laudantium, totam rem aperiam, eaque ipsa quae ab illo inventore veritatis et qu asi architecto beatae vitae dicta sunt explicabo. Nemo enim ipsam voluptatem quia vo luptas sit aspernatur aut odit aut fugit, sed quia consequuntur magni dolores eos qui ratione voluptatem sequi nesciuntque porro quisquam est, qui dolorem ipsumptas sit aspernatur aut odit aut fugit, sed quia consequuntur magni dolores eos qui ratione voluptatem sequi nesciunt. Neque porro quisquam est, qui dolorem ipsum.</p>
  <div class="abs btn" style="left:346px;top:507px;width:56px;height:19px">READ MORE</div>
</section>

<section>
  <h2 class="abs section" style="left:0;width:671px;text-align:center;top:575px">ABOUT QUILLBROOK</h2>
  <p class="abs copy about-intro">Sed ut perspiciatis unde omnis iste natus error sit voluptatem accusantium dolorem que laudantium, totam rem aperiam, eaque ipsa quae ab illo inventore veritatis et qu asi architecto beatae vitae dicta sunt explicabo. Nemo enim ipsam voluptatem quia.</p>

  <div class="abs feature-pic" style="left:91px;top:633px;background:radial-gradient(circle at 50% 40%,#3d8fc8,#2a6a9a 55%,#6aa83a 85%)" role="img" aria-label="Children in a tent at the kids lounge"></div>
  <div class="abs feature-pic" style="left:216px;top:633px;background:radial-gradient(circle at 55% 60%,#e6ee5a,#f2f2f2 40%,#c9c9c9 80%)" role="img" aria-label="Tennis racket and ball"></div>
  <div class="abs feature-pic" style="left:341px;top:633px;background:radial-gradient(circle at 50% 50%,#c98a5a,#efe9e0 45%,#7a5a3e 85%)" role="img" aria-label="Plated dish from the club dining room"></div>
  <div class="abs feature-pic" style="left:465px;top:633px;background:radial-gradient(circle at 60% 50%,#c46a4a,#6a7580 50%,#2e3a44 90%)" role="img" aria-label="Member running in the fitness centre"></div>

  <h3 class="abs feature-name" style="left:86px;top:756px">KID'S LOUNGE</h3>
  <h3 class="abs feature-name" style="left:211px;top:756px">TENNIS</h3>
  <h3 class="abs feature-name" style="left:336px;top:756px">DINING</h3>
  <h3 class="abs feature-name" style="left:460px;top:756px">FITNESS</h3>

  <p class="abs copy feature-text" style="left:96px;top:773px">Sed ut perspiciatis unde omnisste natus error sit voluptatem accusanum dolorem que laudantium, totam rem aperiam, eaque ipsuae ab illo</p>
  <p class="abs copy feature-text" style="left:221px;top:773px">Sed ut perspiciatis unde omnisste natus error sit voluptatem accusanum dolorem que laudantium, totam rem aperiam, eaque ipsuae ab illo</p>
  <p class="abs copy feature-text" style="left:346px;top:773px">Sed ut perspiciatis unde omnisste natus error sit voluptatem accusanum dolorem que laudantium, totam rem aperiam, eaque ipsuae ab illo</p>
  <p class="abs copy feature-text" style="left:470px;top:773px">Sed ut perspiciatis unde omnisste natus error sit voluptatem accusanum dolorem que laudantium, totam rem aperiam, eaque ipsuae ab illo</p>

  <div class="abs col-rule" style="left:210px"></div>
  <div class="abs col-rule" style="left:335px"></div>
  <div class="abs col-rule" style="left:459px"></div>
  <div class="abs double-rule"></div>
</section>

<section>
  <h2 class="abs section" style="left:90px;top:873px">WHO WE ARE</h2>
  <div class="abs who-pic" role="img" aria-label="Watercolour rendering of the clubhouse grounds"></div>
  <p class="abs copy" style="left:253px;top:897px;width:148px">Sed ut perspiciatis unde omnis iste natus error sit voluptatem accusantium doloremque laudantium, totam rem aperiam, eaque ipsa quae ab illo invenre veritatis et quasi architecto beatae vitae dicta sunt explicaboemo enim ipsam voluptatem quia voluptas sit aspernatur aut odit aut fugi voluptatem quia volu ptas sit aspernatur aut odit aut fugit.</p>
  <div class="abs btn" style="left:253px;top:980px;width:57px;height:19px">READ MORE</div>

  <h2 class="abs section" style="left:432px;top:873px">TESTIMONIALS</h2>
  <p class="abs quote"><span class="qmark">&ldquo;</span> Sed ut perspiciatis unde omnis iste natus er ror sit voluptatem accusantium doloremque laudantium, totam rem aperiam, eaque ipsa quaeab illoinventore veritatis et quasi architecto beatae vitae dicta sunt ex licaboemo enim ipsam volup tatem quia voluptas sit aspernatur aut odit aut fugitatem quia voluptas sit aspernatur aut odit aut fugiaut fugitatem quia volu ptas sit aspernatur aut odit aut fugit. <span class="qmark">&rdquo;</span></p>
  <p class="abs cite">ALAN MERCER , CITY NAME</p>
</section>

<footer>
  <div class="abs footer"></div>
  <div class="abs brand foot-brand">QUILLBROOK<br>COUNTRY CLUB</div>

  <h4 class="abs foot-head" style="left:222px;top:1059px">LINKS</h4>
  <div class="abs foot-rule" style="left:224px;top:1075px"></div>
  <ul class="abs foot-list" style="left:222px;top:1082px">
    <li>Guest Info</li><li>Membership</li><li>Golf</li><li>Club House &amp; Amenities</li><li>Wedding &amp; Events</li>
  </ul>

  <h4 class="abs foot-head" style="left:326px;top:1059px">OUR EVENTS</h4>
  <div class="abs foot-rule" style="left:328px;top:1075px"></div>
  <ul class="abs foot-list" style="left:326px;top:1082px">
    <li>Sed ut perspiciatisom</li><li>Giste natus error sit uptat</li><li>Rm accusantium doloremq</li><li>Hlaudantium, totam rem</li><li>Aperiam, eaque ipsa</li><li>Huae ab illo invent.</li>
  </ul>

  <h4 class="abs foot-head" style="left:437px;top:1059px">NEWSLETTER</h4>
  <div class="abs foot-rule" style="left:439px;top:1075px"></div>
  <p class="abs newsletter-text" style="left:437px;top:1082px;width:146px">Lorem ipsum dolor sit amet, consectetur ad ip iscing elit. Nulla in purus nibh.</p>
  <div class="abs email">Email Address:</div>
  <div class="abs btn signup">SIGN UP</div>

  <div class="abs bottom-bar"></div>
  <div class="abs social" style="left:91px"></div>
  <div class="abs social" style="left:110px"></div>
  <div class="abs social" style="left:129px"></div>
  <div class="abs social" style="left:148px"></div>
  <p class="abs legal">&copy; 2015 copyrights are reserved.quillbrook. Privacy Policy. Terms and Conditions</p>
</footer>

</body>
</html>
```